Meridale Bed Company Needs Business Card

Looking for a very nice looking business card. Creative but not extravagant. We sell beds and pillows across the U.S. and need something professional but catchy. I have attached the logo.

Name : Devin Holt
Title : President
Phone : (800) 471-2960
Email: sleep@quilmora.com
Website: www.quilmora.com

Can be single-sided or double-sided
horizontal or vertical

Can use Blues/Greys

Target Market(s)

Mass Market

Industry/Entity Type

Retail

Contact Information for Business Card

Name : Devin Holt
Title : President
Phone : (800) 471-2960
Email: sleep@quilmora.com
Website: www.quilmora.com

Requirements
Must have
• Clean, Modern, Smooth
• Can use Blues/Greys
• On the other side without the information - have something simple like www.quilmora.com or our logo
Nice to have
• Surprise me
Should not have
• Nothing crazy, nothing cluttered

```html
<!DOCTYPE html>
<html lang="en">
<head>
<meta charset="UTF-8">
<title>Meridale Bed Company – Business Card</title>
<link href="https://fonts.googleapis.com/css2?family=Open+Sans:wght@300;400;700&display=swap" rel="stylesheet">
<style>
  :root {
    --canvas-bg: #e9eaec;
    --card-white: #ffffff;
    --brand-blue: #34a4d8;
    --ghost-on-blue: rgba(0, 40, 80, 0.07);
    --ghost-on-white: #f1f2f3;
    --text-white: #ffffff;
  }
  * { margin: 0; padding: 0; box-sizing: border-box; }
  html, body {
    width: 1200px; height: 900px; overflow: hidden;
    background: var(--canvas-bg);
    font-family: "Open Sans", Arial, sans-serif;
  }
  .canvas { position: relative; width: 1200px; height: 900px; }

  .card {
    position: absolute; overflow: hidden;
    background: var(--card-white);
    box-shadow: 0 6px 22px rgba(0,0,0,0.12);
  }
  .wordmark {
    font-family: "Open Sans", Arial, sans-serif;
    font-weight: 300;
    letter-spacing: 1px;
    white-space: nowrap;
    line-height: 1;
  }

  /* Front: contact side */
  .card--front { left: 78px; top: 34px; width: 588px; height: 364px; }
  .card--front .wordmark {
    position: absolute; left: 28px; top: 52px;
    font-size: 104px; color: var(--brand-blue);
  }
  .info-band {
    position: absolute; left: 0; top: 173px; width: 100%; height: 191px;
    background: var(--brand-blue); overflow: hidden;
  }
  .info-band .ghost-mark {
    position: absolute; left: 120px; top: 10px;
    font-size: 170px; color: var(--ghost-on-blue);
  }
  .holder {
    position: absolute; left: 30px; top: 24px; color: var(--text-white);
  }
  .holder__name { font-size: 22px; font-weight: 700; line-height: 1.2; }
  .holder__title { font-size: 16px; font-weight: 400; line-height: 1.3; }
  .contact-list {
    position: absolute; left: 30px; top: 98px; list-style: none;
    color: var(--text-white); font-size: 15px;
  }
  .contact-list li { display: flex; align-items: center; height: 25px; }
  .contact-list svg { width: 12px; height: 12px; margin-right: 10px; fill: var(--text-white); }

  /* Back: logo side */
  .card--back { left: 388px; top: 506px; width: 567px; height: 351px; }
  .card--back .ghost-mark {
    position: absolute; left: -10px;
    font-size: 150px; color: var(--ghost-on-white);
  }
  .ghost-mark--top { top: -38px; }
  .ghost-mark--bottom { top: 232px; }
  .logo-band {
    position: absolute; left: 0; top: 110px; width: 100%; height: 129px;
    background: var(--brand-blue);
    display: flex; align-items: center; justify-content: center;
  }
  .logo-band .wordmark { font-size: 92px; color: var(--text-white); margin-top: -14px; }
</style>
</head>
<body>
<main class="canvas">

  <section class="card card--front" aria-label="Business card front">
    <div class="wordmark">quilmora</div>
    <div class="info-band">
      <div class="wordmark ghost-mark" aria-hidden="true">quilmora</div>
      <div class="holder">
        <p class="holder__name">Devin Holt</p>
        <p class="holder__title">President</p>
      </div>
      <ul class="contact-list">
        <li>
          <svg viewBox="0 0 24 24" aria-hidden="true"><path d="M6.6 10.8c1.4 2.8 3.8 5.1 6.6 6.6l2.2-2.2c.3-.3.7-.4 1-.2 1.1.4 2.3.6 3.6.6.6 0 1 .4 1 1V20c0 .6-.4 1-1 1C10.6 21 3 13.4 3 4c0-.6.4-1 1-1h3.5c.6 0 1 .4 1 1 0 1.3.2 2.5.6 3.6.1.3 0 .7-.2 1L6.6 10.8z"/></svg>
          (800) 471-2960
        </li>
        <li>
          <svg viewBox="0 0 24 24" aria-hidden="true"><path d="M2 5h20v14H2z M3 6l9 7 9-7" fill="none" stroke="#fff" stroke-width="0"/><path d="M2 5h20v2l-10 7L2 7z M2 9l10 7 10-7v10H2z"/></svg>
          sleep@quilmora.com
        </li>
        <li>
          <svg viewBox="0 0 24 24" aria-hidden="true"><circle cx="12" cy="12" r="10"/><path d="M2 12h20M12 2c3 3 3 17 0 20M12 2c-3 3-3 17 0 20" fill="none" stroke="#34a4d8" stroke-width="1.6"/></svg>
          www.quilmora.com
        </li>
      </ul>
    </div>
  </section>

  <section class="card card--back" aria-label="Business card back">
    <div class="wordmark ghost-mark ghost-mark--top" aria-hidden="true">quilmora</div>
    <div class="logo-band">
      <div class="wordmark">quilmora</div>
    </div>
    <div class="wordmark ghost-mark ghost-mark--bottom" aria-hidden="true">quilmora</div>
  </section>

</main>
</body>
</html>
```